Business Card Design for company

We want new business cards. We'd like something different-- yet still highly professional. Our tagline is Providing leadership, delivering success. Stock photos are ok, as long as they are relevant and look upscale.

Target Market(s)

Architecture/Business Management Consulting/Engineering Consulting

Contact Information for Business Card

dark gray background with pops of blue might be good, but you tell me. You're the designers. Rounded corners might be nice, but again, you tell me.

Font styles to use
Serif
Sans Serif

Colors
3276b5
5c5c5c
9d9d9d
fbfbfb

Requirements
Nice to have
• Something different, but still very professional.

```html
<!DOCTYPE html>
<html lang="en">
<head>
<meta charset="utf-8">
<title>Korvan Partners — Business Cards</title>
<link href="https://fonts.googleapis.com/css2?family=Open+Sans:wght@400;600&display=swap" rel="stylesheet">
<style>
  :root {
    --brand-blue: #3276b5;
    --blue-light: #5597cc;
    --charcoal: #5c5c5c;
    --silver: #9d9d9d;
    --paper: #fbfbfb;
    --backdrop: #d6d6d6;
    --faint: #dfe5ec;
  }
  * { box-sizing: border-box; margin: 0; padding: 0; }
  html, body { width: 1200px; height: 864px; overflow: hidden; }
  body {
    background: var(--backdrop);
    font-family: "Open Sans", Arial, sans-serif;
    position: relative;
  }
  .card {
    position: absolute;
    left: 290px;
    width: 620px;
    height: 354px;
    background: var(--paper);
    box-shadow: 0 6px 18px rgba(0,0,0,0.18);
    overflow: hidden;
  }
  .card--front { top: 50px; }
  .card--back { top: 460px; }

  .wordmark {
    font-weight: 600;
    color: var(--brand-blue);
    letter-spacing: 0.02em;
    white-space: nowrap;
  }
  .card--front .wordmark--primary {
    position: absolute;
    left: 46px;
    top: 150px;
    font-size: 38px;
  }
  .card--front .wordmark--ghost {
    position: absolute;
    left: 382px;
    top: 86px;
    font-size: 24px;
    color: var(--faint);
  }

  .back-top {
    position: absolute;
    inset: 0 0 auto 0;
    height: 150px;
    display: flex;
    align-items: center;
    justify-content: center;
  }
  .back-top .wordmark { font-size: 30px; margin-top: 30px; }

  .band {
    position: absolute;
    left: 0; right: 0;
    top: 150px;
    height: 12px;
    background: var(--charcoal);
  }
  .band__accent {
    position: absolute;
    left: 210px;
    width: 200px;
    top: 0; bottom: 0;
    background: var(--silver);
  }
  .back-panel {
    position: absolute;
    left: 0; right: 0;
    top: 162px; bottom: 0;
    background: linear-gradient(100deg, var(--brand-blue) 0%, var(--blue-light) 45%, var(--brand-blue) 100%);
    color: var(--paper);
  }
  .contact-list {
    list-style: none;
    position: absolute;
    left: 34px;
    top: 26px;
    font-size: 14px;
    line-height: 24px;
  }
  .contact-list li { display: flex; align-items: center; gap: 10px; }
  .contact-list svg { width: 14px; height: 14px; flex: none; }
  .holder {
    position: absolute;
    right: 40px;
    bottom: 44px;
    text-align: right;
  }
  .holder__name { font-size: 21px; font-weight: 600; }
  .holder__role { font-size: 15px; }
</style>
</head>
<body>

<section class="card card--front" aria-label="Card front">
  <p class="wordmark wordmark--primary">Korvan Partners</p>
  <p class="wordmark wordmark--ghost" aria-hidden="true">Korvan Partners</p>
</section>

<section class="card card--back" aria-label="Card back">
  <div class="back-top">
    <p class="wordmark">Korvan Partners</p>
  </div>
  <div class="band"><span class="band__accent"></span></div>
  <div class="back-panel">
    <ul class="contact-list">
      <li>
        <svg viewBox="0 0 14 14"><rect width="14" height="14" rx="2" fill="#fbfbfb"/><path d="M4 3.5c.6-.4 1.2 0 1.5.7l.4 1c.1.4-.1.7-.4.9l-.4.3c.4 1 1.2 1.8 2.2 2.2l.3-.4c.2-.3.5-.5.9-.4l1 .4c.7.3 1.1.9.7 1.5-.5.8-1.4 1.2-2.3.9C5.6 9.8 4.2 8.4 3.4 6.2c-.3-.9.1-1.9.6-2.7z" fill="#3276b5"/></svg>
        +0000-0000-0000
      </li>
      <li>
        <svg viewBox="0 0 14 14"><rect width="14" height="14" rx="2" fill="#fbfbfb"/><rect x="2.5" y="4" width="9" height="6" fill="none" stroke="#3276b5" stroke-width="1.2"/><path d="M2.5 4l4.5 3.5L11.5 4" fill="none" stroke="#3276b5" stroke-width="1.2"/></svg>
        info@korvanpartners.com
      </li>
      <li>
        <svg viewBox="0 0 14 14"><rect width="14" height="14" rx="2" fill="#fbfbfb"/><circle cx="7" cy="7" r="4.2" fill="none" stroke="#3276b5" stroke-width="1.2"/><path d="M2.8 7h8.4M7 2.8c-2 2.6-2 5.8 0 8.4M7 2.8c2 2.6 2 5.8 0 8.4" fill="none" stroke="#3276b5" stroke-width="1"/></svg>
        www.korvanpartners.com
      </li>
      <li>
        <svg viewBox="0 0 14 14"><rect width="14" height="14" rx="2" fill="#fbfbfb"/><path d="M7 12s-3.5-3.6-3.5-6A3.5 3.5 0 0 1 10.5 6c0 2.4-3.5 6-3.5 6z" fill="#3276b5"/><circle cx="7" cy="6" r="1.3" fill="#fbfbfb"/></svg>
        Suite 210, 48 Alder Row, Bristol
      </li>
    </ul>
    <div class="holder">
      <p class="holder__name">Daniel Reyes</p>
      <p class="holder__role">Owner</p>
    </div>
  </div>
</section>

</body>
</html>
```